Business Card Design for Training Business

Clear Path Coaching is a new business that delivers training and other services with a focus on topics related to mental health and wellbeing, for example, Wellmind Response Course, Resilience etc. We have a strong focus on evidence-based psychology and neuroscience. I have a logo which I will upload with the brief, so please consider colours that work well with the logo.
Target Market(s)
Adults, workplaces (particularly government and not-for-profits)
Industry/Entity Type
Business
Contact Information for Business Card
Head Strong TrainingSamantha SellwoodDirector0438 770 850sam@headstrongtraining.com.auwww.headstrongtraining.com.au

```html
<!DOCTYPE html>
<html lang="en">
<head>
<meta charset="utf-8">
<title>Clear Path Coaching – Business Card</title>
<link rel="stylesheet" href="https://fonts.googleapis.com/css2?family=Questrial&display=swap">
<style>
  :root {
    --teal: #21b8bd;
    --teal-soft: #3ec4c8;
    --paper: #f7f7f6;
    --brown: #4a3c36;
    --ink: #3d3a39;
    --backdrop: #3a3a3a;
    --white: #ffffff;
  }
  * { box-sizing: border-box; margin: 0; padding: 0; }
  html, body {
    width: 1200px;
    height: 750px;
    overflow: hidden;
    background: var(--backdrop);
    font-family: "Questrial", "Century Gothic", sans-serif;
  }
  .canvas { position: relative; width: 1200px; height: 750px; }

  .card {
    position: absolute;
    left: 371px;
    width: 461px;
    height: 262px;
    border-radius: 12px;
    overflow: hidden;
  }
  .card--front { top: 106px; background: var(--teal); }
  .card--back { top: 388px; background: var(--teal); }

  .card__bands { position: absolute; inset: 0; }

  .brand {
    position: absolute;
    left: 34px;
    top: 92px;
    width: 176px;
    text-align: center;
    color: var(--ink);
    font-size: 15px;
    letter-spacing: 3px;
    line-height: 1.5;
    text-transform: uppercase;
  }
  .brand__dot {
    display: block;
    width: 46px;
    height: 46px;
    margin: 0 auto 12px;
    border-radius: 50%;
    background: var(--teal);
  }

  .contact {
    position: absolute;
    left: 218px;
    top: 77px;
    color: var(--ink);
  }
  .contact__name {
    color: var(--teal);
    font-size: 18px;
    font-weight: 400;
    letter-spacing: 0.3px;
  }
  .contact__role { font-size: 13px; margin-top: 4px; }
  .contact__list {
    list-style: none;
    font-size: 12px;
    line-height: 18.5px;
    margin-top: 12px;
  }
  .contact__label { color: var(--teal); }

  .back-brand {
    position: absolute;
    left: 0;
    right: 0;
    top: 66px;
    text-align: center;
    color: var(--white);
    font-size: 17px;
    letter-spacing: 4px;
    text-transform: uppercase;
  }
  .back-brand__ring {
    display: block;
    width: 70px;
    height: 70px;
    margin: 0 auto 16px;
    border: 2px solid var(--white);
    border-radius: 50%;
  }
  .back-web {
    position: absolute;
    left: 0;
    right: 0;
    top: 224px;
    text-align: center;
    color: var(--white);
    font-size: 12.5px;
  }
</style>
</head>
<body>
<main class="canvas">

  <section class="card card--front" aria-label="Business card front">
    <svg class="card__bands" width="461" height="262" viewBox="0 0 461 262" aria-hidden="true">
      <path d="M0 38 Q230 -8 461 38 L461 226 Q230 272 0 226 Z" fill="var(--white)"/>
      <path d="M0 39 Q230 -6 461 39 L461 225 Q230 270 0 225 Z" fill="var(--paper)"/>
      <path d="M0 38 Q230 -8 461 38" fill="none" stroke="var(--brown)" stroke-width="2"/>
      <path d="M0 226 Q230 272 461 226" fill="none" stroke="var(--brown)" stroke-width="2"/>
      <path d="M0 34 Q230 -12 461 34" fill="none" stroke="var(--white)" stroke-width="1"/>
      <path d="M0 230 Q230 276 461 230" fill="none" stroke="var(--white)" stroke-width="1"/>
    </svg>

    <div class="brand">
      <span class="brand__dot"></span>
      Clear Path<br>Coaching
    </div>

    <div class="contact">
      <h1 class="contact__name">Rebecca Tanfield</h1>
      <p class="contact__role">Director</p>
      <ul class="contact__list">
        <li><span class="contact__label">P:</span> 0491 362 517</li>
        <li>bec@clearpathcoaching.example.au</li>
        <li>www.clearpathcoaching.example.au</li>
      </ul>
    </div>
  </section>

  <section class="card card--back" aria-label="Business card back">
    <div class="back-brand">
      <span class="back-brand__ring"></span>
      Clear Path Coaching
    </div>
    <p class="back-web">www.clearpathcoaching.example.au</p>
  </section>

</main>
</body>
</html>
```